Need Web Design for Business Process Outsourcing Company (Quorvane)

Quorvane is a business process outsourcing company. Need a simple site similar to http://www.tallowbrinkhire.com/ but with a more professional and credible look. New to the process; not sure where to start and comparing my options. Please let me know what my options are if I choose to go with you. Logo is attached for your reference. Please use same colorway

Reason: I want the final product to be coded. Please confirm you will be able to code final design.

Industry/Entity Type

Business

Coding

Coded - Design and coding required

```html
<!DOCTYPE html>
<html lang="en">
<head>
<meta charset="utf-8">
<title>Quorvane Services</title>
<link href="https://fonts.googleapis.com/css2?family=Roboto:wght@400;500;700&family=Oswald:wght@500&display=swap" rel="stylesheet">
<style>
:root{
  --navy:#0b5a8c;
  --navy-dark:#094d79;
  --bright:#1a90d0;
  --accent:#1f9ad9;
  --text:#666;
  --light:#efefef;
  --white:#fff;
}
*{box-sizing:border-box;margin:0;padding:0}
html,body{width:1200px;height:3237px;overflow:hidden}
body{font-family:"Roboto",Arial,sans-serif;color:var(--text);background:var(--white);position:relative}
section,header,footer{position:absolute;left:0;width:1200px}
a{text-decoration:none}
.btn{position:absolute;background:var(--bright);color:var(--white);font-size:20px;font-weight:500;display:flex;align-items:center;justify-content:center;text-transform:uppercase;text-decoration:none}

/* header */
.site-header{top:0;height:125px;background:var(--white)}
.brand{position:absolute;left:78px;top:22px;display:flex;align-items:center;gap:14px}
.brand-square{width:62px;height:62px;background:var(--navy)}
.brand-name{font-size:50px;font-weight:700;color:var(--navy);line-height:1}
.contact-circle{position:absolute;width:56px;height:56px;border-radius:50%;background:var(--navy);display:flex;align-items:center;justify-content:center}
.contact-label{position:absolute;font-size:16px;color:#444}
.contact-value{position:absolute;color:var(--bright)}
.main-nav{position:absolute;left:78px;top:125px;width:1044px;height:61px;background:var(--navy);display:flex;align-items:center;justify-content:space-between;padding-right:14px;z-index:2}
.main-nav a{color:#fff;font-size:15px;text-transform:uppercase}
.main-nav a.active{background:var(--bright);height:61px;width:105px;display:flex;align-items:center;justify-content:center}

/* hero */
.hero{top:168px;height:518px}
.hero-photo{position:absolute;inset:0;background:linear-gradient(100deg,#c9d2da 0%,#8fa3b4 40%,#5d7487 70%,#b6c2cc 100%)}
.hero-title{position:absolute;top:170px;width:100%;text-align:center;font-family:"Oswald",sans-serif;font-size:82px;font-weight:500;color:#fff;line-height:1}
.hero-sub{position:absolute;top:256px;left:175px;width:850px;text-align:center;font-size:17px;line-height:28px;color:#111}
.hero .btn{left:479px;top:326px;width:244px;height:58px}
.hero-arrow{position:absolute;top:218px;width:48px;height:48px;border-radius:50%;border:2px solid rgba(255,255,255,.7)}

/* welcome */
.welcome{top:686px;height:492px}
.section-title{position:absolute;width:100%;text-align:center;color:var(--navy);font-size:40px;font-weight:500}
.lead{position:absolute;text-align:center;font-size:14.5px;line-height:26px;color:var(--text)}
.services{position:absolute;left:78px;top:274px;width:1044px;height:156px;display:flex}
.service{flex:1;position:relative;border:1px solid #e8e8e8;border-left:none;background:#fff}
.service:first-child{border-left:1px solid #e8e8e8}
.service.active{background:var(--light)}
.service-icon{position:absolute;left:50%;top:-58px;margin-left:-56px;width:112px;height:112px;border-radius:50%;background:var(--navy);display:flex;align-items:center;justify-content:center}
.service-name{position:absolute;top:80px;width:100%;text-align:center;font-size:19px;color:var(--navy);line-height:24px;text-transform:uppercase}

/* strengths */
.strengths{top:1178px;height:419px;background:var(--navy)}
.strength h3{position:absolute;font-size:19px;font-weight:400;color:var(--accent);text-transform:uppercase}
.strength p{position:absolute;font-size:14.5px;line-height:26px;color:#e3edf5}
.tile-back{position:absolute;width:92px;height:92px;background:#1a7fc0}
.tile{position:absolute;width:104px;height:104px;background:#fff;border-radius:6px;display:flex;align-items:center;justify-content:center}

/* global */
.global{top:1597px;height:367px;background:var(--light)}
.map-area{position:absolute;left:78px;top:75px;width:422px;height:195px;border-radius:50%;background:radial-gradient(ellipse at center,#e4e4e4,#bdbdbd)}
.global h2{position:absolute;left:540px;top:54px;font-size:39px;font-weight:500;color:var(--navy)}
.global p{position:absolute;left:540px;top:108px;width:580px;font-size:14.5px;line-height:26px}

/* news */
.news{top:1964px;height:496px}
.news-grid{position:absolute;left:78px;top:121px;width:1044px;display:flex;justify-content:space-between}
.news-item{width:250px}
.news-photo{height:166px;background:linear-gradient(135deg,#54708a,#1e3347)}
.news-item:nth-child(2) .news-photo{background:linear-gradient(135deg,#c7cdd2,#6b7379)}
.news-item:nth-child(3) .news-photo{background:linear-gradient(135deg,#3c4650,#8a949b)}
.news-item:nth-child(4) .news-photo{background:linear-gradient(135deg,#dfe3e6,#2f4254)}
.news-item h4{margin-top:22px;font-size:16.5px;font-weight:500;color:var(--navy)}
.news-date{margin-top:10px;font-size:14.5px;color:var(--navy);display:flex;align-items:center;gap:6px}
.news-item p{margin-top:6px;font-size:14.5px;line-height:26px}

/* call to action */
.cta{top:2460px;height:352px;background:var(--light)}
.cta h2{position:absolute;top:48px;width:100%;text-align:center;font-size:32px;font-weight:500;color:var(--navy);line-height:48px}
.cta .btn{left:511px;top:235px;width:177px;height:56px}

/* footer */
.site-footer{top:2812px;height:360px;background:var(--navy);color:#dfe9f1}
.footer-brand{position:absolute;left:78px;top:36px;display:flex;align-items:center;gap:12px}
.footer-brand .brand-square{width:56px;height:56px;background:#fff}
.footer-brand .brand-name{color:#fff;font-size:46px}
.footer-text{position:absolute;left:78px;width:320px;font-size:14px;line-height:26px}
.footer-head{position:absolute;top:30px;font-size:19px;color:var(--accent);text-transform:uppercase}
.touch-row{position:absolute;left:434px;display:flex;gap:16px;font-size:14px;line-height:26px}
.social{position:absolute;top:282px;width:44px;height:44px;border-radius:50%;border:2px solid var(--accent)}
.social.filled{background:var(--bright);border-color:var(--bright)}
.field{position:absolute;left:790px;width:332px;background:var(--navy-dark);font-size:14px;color:#fff;padding:11px 12px}
.site-footer .btn{left:790px;top:274px;width:144px;height:54px}
.copyright{position:absolute;left:0;top:3172px;width:1200px;height:65px;background:var(--bright);color:#fff;font-size:14px;display:flex;align-items:center;justify-content:center}
.copyright span{color:#0b3f63;margin:0 4px}
</style>
</head>
<body>

<header class="site-header">
  <div class="brand"><span class="brand-square"></span><span class="brand-name">Quorvane</span></div>
  <div class="contact-circle" style="left:572px;top:37px">
    <svg width="26" height="20" viewBox="0 0 26 20"><rect x="1" y="1" width="24" height="18" rx="2" fill="none" stroke="#fff" stroke-width="2"/><path d="M1 2l12 9 12-9" fill="none" stroke="#fff" stroke-width="2"/></svg>
  </div>
  <div class="contact-label" style="left:645px;top:38px">EMAIL US :</div>
  <div class="contact-value" style="left:645px;top:64px;font-size:22px">info@quorvane.com</div>
  <div class="contact-circle" style="left:846px;top:37px">
    <svg width="24" height="24" viewBox="0 0 24 24"><path d="M5 2l4 1 1 5-3 2a12 12 0 006 6l2-3 5 1 1 4-3 3C9 22 2 15 2 5z" fill="none" stroke="#fff" stroke-width="2" stroke-linejoin="round"/></svg>
  </div>
  <div class="contact-label" style="left:921px;top:34px">REQUEST CALL BACK :</div>
  <div class="contact-value" style="left:921px;top:56px;font-size:31px">123 456 7890</div>
</header>

<nav class="main-nav">
  <a class="active" href="#">Home</a>
  <a href="#">About</a>
  <a href="#">Our Services</a>
  <a href="#">Our Strategy</a>
  <a href="#">Our Experiency</a>
  <a href="#">Security</a>
  <a href="#">News</a>
  <a href="#">Contact</a>
</nav>

<section class="hero">
  <div class="hero-photo" role="img" aria-label="Photo of people working together at a laptop in an office"></div>
  <h1 class="hero-title">QUORVANE SERVICES</h1>
  <p class="hero-sub">Lorem Ipsum is simply dummy text of the printing and typesetting industry. Lorem Ipsum has been the industry's standard dummy text ever since the 1500s, when an unknown</p>
  <a class="btn" href="#">Contact us know</a>
  <span class="hero-arrow" style="left:19px"><svg width="44" height="44" viewBox="0 0 44 44"><path d="M25 14l-8 8 8 8" fill="none" stroke="#fff" stroke-width="2"/></svg></span>
  <span class="hero-arrow" style="left:1137px"><svg width="44" height="44" viewBox="0 0 44 44"><path d="M19 14l8 8-8 8" fill="none" stroke="#fff" stroke-width="2"/></svg></span>
</section>

<section class="welcome">
  <h2 class="section-title" style="top:56px">WELCOME TO QUORVANE SERVICES</h2>
  <p class="lead" style="left:140px;top:118px;width:920px">Lorem Ipsum is simply dummy text of the printing and typesetting industry. Lorem Ipsum has been the industry's standard dummy text ever since the 1500s, when an unknown printer took a galley of type and scrambled it to make a type specimen book. It has survived not only five centuries, but also the leap into electronic typesetting, remaining essentially unchanged.</p>
  <div class="services">
    <div class="service active">
      <div class="service-icon"><svg width="60" height="60" viewBox="0 0 60 60" fill="none" stroke="#fff" stroke-width="3"><circle cx="30" cy="30" r="14"/><path d="M12 32v-4a18 18 0 0136 0v4"/><rect x="8" y="28" width="7" height="12" rx="2" fill="#fff"/><rect x="45" y="28" width="7" height="12" rx="2" fill="#fff"/><path d="M48 40c0 6-6 8-14 8"/></svg></div>
      <div class="service-name">Customer<br>Service</div>
    </div>
    <div class="service">
      <div class="service-icon"><svg width="60" height="60" viewBox="0 0 60 60" fill="none" stroke="#fff" stroke-width="3" stroke-linejoin="round"><path d="M8 14h8l6 24h24l5-18H19"/><circle cx="25" cy="46" r="3" fill="#fff"/><circle cx="43" cy="46" r="3" fill="#fff"/><path d="M24 26h24M25 32h21"/></svg></div>
      <div class="service-name">Ecommerce</div>
    </div>
    <div class="service">
      <div class="service-icon"><svg width="60" height="60" viewBox="0 0 60 60" fill="none" stroke="#fff" stroke-width="3"><rect x="10" y="10" width="40" height="32"/><path d="M22 18l16 16M38 18L22 34M24 50h12M30 42v8"/></svg></div>
      <div class="service-name">Creative</div>
    </div>
    <div class="service">
      <div class="service-icon"><svg width="60" height="60" viewBox="0 0 60 60" fill="none" stroke="#fff" stroke-width="3"><path d="M22 36a12 12 0 1116 0v6H22z"/><path d="M24 48h12M30 6v4M12 14l3 3M48 14l-3 3M6 28h4M50 28h4"/></svg></div>
      <div class="service-name">IT Solutions</div>
    </div>
    <div class="service">
      <div class="service-icon"><svg width="64" height="60" viewBox="0 0 64 60" fill="#fff"><circle cx="32" cy="18" r="8"/><path d="M20 44a12 12 0 0124 0z"/><circle cx="14" cy="24" r="6"/><path d="M4 44a10 10 0 0118-2v2z"/><circle cx="50" cy="24" r="6"/><path d="M42 44v-2a10 10 0 0118 2z"/></svg></div>
      <div class="service-name">Human<br>Resources</div>
    </div>
  </div>
</section>

<section class="strengths">
  <div class="strength">
    <h3 style="left:178px;top:91px">Reinventing Services</h3>
    <p style="left:172px;top:121px;width:258px;text-align:right">Lorem Ipsum is simply dummy text of the printing and typesetting industry. Lorem Ipsum has been the.</p>
  </div>
  <div class="strength">
    <h3 style="left:766px;top:91px">Our Facilites</h3>
    <p style="left:766px;top:121px;width:258px">Lorem Ipsum is simply dummy text of the printing and typesetting industry. Lorem Ipsum has been the.</p>
  </div>
  <div class="strength">
    <h3 style="left:298px;top:241px">Our People</h3>
    <p style="left:172px;top:271px;width:258px;text-align:right">Lorem Ipsum is simply dummy text of the printing and typesetting industry. Lorem Ipsum has been the.</p>
  </div>
  <div class="strength">
    <h3 style="left:766px;top:241px">Success Stoies</h3>
    <p style="left:766px;top:271px;width:258px">Lorem Ipsum is simply dummy text of the printing and typesetting industry. Lorem Ipsum has been the.</p>
  </div>

  <span class="tile-back" style="left:478px;top:64px"></span>
  <span class="tile-back" style="left:618px;top:64px"></span>
  <span class="tile-back" style="left:478px;top:220px"></span>
  <span class="tile-back" style="left:618px;top:220px"></span>

  <div class="tile" style="left:452px;top:91px"><svg width="70" height="70" viewBox="0 0 70 70" fill="var(--bright)"><circle cx="26" cy="28" r="16"/><circle cx="26" cy="28" r="6" fill="#fff"/><circle cx="50" cy="50" r="10"/><circle cx="50" cy="50" r="4" fill="#fff"/></svg></div>
  <div class="tile" style="left:643px;top:91px"><svg width="70" height="70" viewBox="0 0 70 70" fill="var(--bright)"><rect x="12" y="20" width="20" height="40"/><rect x="32" y="10" width="24" height="50"/><g fill="#fff"><rect x="37" y="16" width="5" height="5"/><rect x="46" y="16" width="5" height="5"/><rect x="37" y="27" width="5" height="5"/><rect x="46" y="27" width="5" height="5"/><rect x="37" y="38" width="5" height="5"/><rect x="46" y="38" width="5" height="5"/><rect x="17" y="28" width="10" height="4"/><rect x="17" y="38" width="10" height="4"/></g></svg></div>
  <div class="tile" style="left:452px;top:248px"><svg width="70" height="70" viewBox="0 0 70 70" fill="none" stroke="var(--bright)" stroke-width="5" stroke-linejoin="round"><path d="M8 52l18-16 12 10 20-22"/><path d="M48 22h12v12"/></svg></div>
  <div class="tile" style="left:643px;top:248px"><svg width="70" height="70" viewBox="0 0 70 70" fill="var(--bright)"><circle cx="35" cy="22" r="10"/><path d="M20 56a15 15 0 0130 0z"/><circle cx="16" cy="30" r="7"/><path d="M4 56a12 12 0 0118-6v6z"/><circle cx="54" cy="30" r="7"/><path d="M48 56v-6a12 12 0 0118 6z"/></svg></div>
</section>

<section class="global">
  <div class="map-area" role="img" aria-label="World map showing office locations"></div>
  <h2>GLOBAL PRESENCE</h2>
  <p>Lorem Ipsum is simply dummy text of the printing and typesetting industry. Lorem Ipsum has been the industry's standard dummy text ever since the 1500s, when an unknown printer took a galley of type and scrambled it to make a type specimen book. It has survived not only five centuries, but also the leap into electronic typesetting, remaining essentially unchanged.</p>
  <a class="btn" href="#" style="left:540px;top:252px;width:166px;height:54px">Know more</a>
</section>

<section class="news">
  <h2 class="section-title" style="top:52px">LATEST NEWS</h2>
  <div class="news-grid">
    <article class="news-item">
      <div class="news-photo" role="img" aria-label="Photo of a hand touching a digital interface"></div>
      <h4>LOREM IPSUM IS THE SIMPLE</h4>
      <div class="news-date"><svg width="14" height="14" viewBox="0 0 14 14"><rect x="1" y="2" width="12" height="11" fill="none" stroke="currentColor" stroke-width="1.5"/><path d="M1 5h12" stroke="currentColor" stroke-width="1.5"/></svg>09 Nov 2016</div>
      <p>Lorem Ipsum is simply dummy text of the printing and typesetting industry. Lorem Ipsum has been.</p>
    </article>
    <article class="news-item">
      <div class="news-photo" role="img" aria-label="Photo of hands working on a laptop at a desk"></div>
      <h4>LOREM IPSUM IS THE SIMPLE</h4>
      <div class="news-date"><svg width="14" height="14" viewBox="0 0 14 14"><rect x="1" y="2" width="12" height="11" fill="none" stroke="currentColor" stroke-width="1.5"/><path d="M1 5h12" stroke="currentColor" stroke-width="1.5"/></svg>10 Nov 2016</div>
      <p>Lorem Ipsum is simply dummy text of the printing and typesetting industry. Lorem Ipsum has been.</p>
    </article>
    <article class="news-item">
      <div class="news-photo" role="img" aria-label="Photo of a modern office interior"></div>
      <h4>LOREM IPSUM IS THE SIMPLE</h4>
      <div class="news-date"><svg width="14" height="14" viewBox="0 0 14 14"><rect x="1" y="2" width="12" height="11" fill="none" stroke="currentColor" stroke-width="1.5"/><path d="M1 5h12" stroke="currentColor" stroke-width="1.5"/></svg>11 Nov 2016</div>
      <p>Lorem Ipsum is simply dummy text of the printing and typesetting industry. Lorem Ipsum has been.</p>
    </article>
    <article class="news-item">
      <div class="news-photo" role="img" aria-label="Photo of a business handshake"></div>
      <h4>LOREM IPSUM IS THE SIMPLE</h4>
      <div class="news-date"><svg width="14" height="14" viewBox="0 0 14 14"><rect x="1" y="2" width="12" height="11" fill="none" stroke="currentColor" stroke-width="1.5"/><path d="M1 5h12" stroke="currentColor" stroke-width="1.5"/></svg>12 Nov 2016</div>
      <p>Lorem Ipsum is simply dummy text of the printing and typesetting industry. Lorem Ipsum has been.</p>
    </article>
  </div>
</section>

<section class="cta">
  <h2>PASSIONATE ABOUT ENGAGING WITH CLIENTS AND<br>GROWING BUSINESS ?</h2>
  <p class="lead" style="left:120px;top:150px;width:960px">Lorem Ipsum is simply dummy text of the printing and typesetting industry. Lorem Ipsum has been the industry's standard dummy text ever since the 1500s, when an unknown printer took a galley of type and scrambled it to make a type specimen book. It has survived not only five centuries, but also the leap into electronic typesetting, remaining essentially unchanged.</p>
  <a class="btn" href="#">Apply know</a>
</section>

<footer class="site-footer">
  <div class="footer-brand"><span class="brand-square"></span><span class="brand-name">Quorvane</span></div>
  <p class="footer-text" style="top:122px">Lorem Ipsum is simply dummy text of the printing and typesetting industry Lorem Ipsum has been the industry's standard dummy text ever since the 1500s, when an unknown printer.</p>
  <p class="footer-text" style="top:236px">Lorem Ipsum is simply dummy text of the printing and typesetting industry &nbsp;has been the industry's standard dummy..</p>

  <div class="footer-head" style="left:434px">Get in touch</div>
  <div class="touch-row" style="top:72px">
    <svg width="24" height="22" viewBox="0 0 24 22"><path d="M1 4l7-3 8 3 7-3v17l-7 3-8-3-7 3z M8 1v17M16 4v17" fill="none" stroke="#fff" stroke-width="1.6"/></svg>
    <div><div style="font-size:18px;color:#fff;font-weight:500">QUORVANE SERVICES</div><div style="width:260px;margin-top:4px">Lorem Ipsum is simply dummy text of the printing and typesetting industry. Lorem Ipsum has been.</div></div>
  </div>
  <div class="touch-row" style="top:198px">
    <svg width="22" height="22" viewBox="0 0 24 24"><path d="M5 2l4 1 1 5-3 2a12 12 0 006 6l2-3 5 1 1 4-3 3C9 22 2 15 2 5z" fill="none" stroke="#fff" stroke-width="1.6"/></svg>123 456 7890
  </div>
  <div class="touch-row" style="top:236px">
    <svg width="22" height="18" viewBox="0 0 26 20"><rect x="1" y="1" width="24" height="18" rx="2" fill="none" stroke="#fff" stroke-width="2"/><path d="M1 2l12 9 12-9" fill="none" stroke="#fff" stroke-width="2"/></svg>info@quorvaneservices.com
  </div>
  <span class="social filled" style="left:434px"></span>
  <span class="social" style="left:491px"></span>
  <span class="social" style="left:548px"></span>

  <div class="footer-head" style="left:790px">Get afree quote</div>
  <div class="field" style="top:75px;height:44px">Name*</div>
  <div class="field" style="top:123px;height:44px">Email*</div>
  <div class="field" style="top:170px;height:93px">Phone*</div>
  <a class="btn" href="#">Submit</a>
</footer>
<div class="copyright">© <span>QUORVANE SERVICES</span> - 2016 All rights reserved.</div>

</body>
</html>
```